Resposive web site in 4 languages + image gallery + logo design

We need a web page, which will work on all devices.
I have uploaded web page concept.
Company name: Praxelun
Industry/Entity Type
It Company
Logo Text
quality matters
Coding
Coded - Design and coding required
Number of Pages Required
1 page

```html
<!DOCTYPE html>
<html lang="en">
<head>
<meta charset="utf-8">
<title>Praxelun – Construction &amp; Renovation</title>
<link href="https://fonts.googleapis.com/css2?family=Lato:wght@400;700&family=Philosopher&display=swap" rel="stylesheet">
<style>
:root{
  --orange:#f2652b;
  --black:#0b0b0b;
  --dark:#1c1c1c;
  --ink:#2a2a2a;
  --text:#555;
  --grey-bg:#e6e6e6;
  --topbar:#e8e8e8;
  --white:#fff;
  --footer:#141414;
  --field:#2a2a2a;
}
*{box-sizing:border-box;margin:0;padding:0}
html,body{width:1200px;height:2659px;overflow:hidden}
body{font-family:"Lato",sans-serif;color:var(--text);background:var(--white);position:relative}
.abs{position:absolute}
.btn{background:var(--orange);color:var(--white);font-weight:700;border-radius:3px;display:inline-block;text-align:center}

/* top bar */
.topbar{left:0;top:0;width:1200px;height:43px;background:var(--topbar)}
.topbar .contact{left:100px;top:12px;font-size:14px;color:var(--orange);display:flex;gap:28px}
.topbar .contact span{display:flex;align-items:center;gap:8px}
.socials{display:flex;gap:13px}
.topbar .socials{right:94px;top:7px}
.social-dot{width:27px;height:27px;border:2px solid var(--orange);border-radius:50%}

/* nav */
.nav{left:0;top:43px;width:1200px;height:95px;background:var(--black)}
.brand{display:flex;align-items:center;gap:12px;font-family:"Lato",sans-serif;font-weight:700;color:var(--white)}
.brand .mark{background:var(--orange)}
.nav .brand{left:100px;top:28px;font-size:30px}
.nav .brand .mark{width:34px;height:34px}
.menu{left:528px;top:0;height:95px;display:flex;align-items:center;font-size:13px;color:var(--orange);white-space:nowrap}
.menu li{list-style:none;display:flex;align-items:center}
.menu li+li::before{content:"";width:7px;height:7px;border-radius:50%;background:#555;margin:0 29px}
.lang{left:988px;top:0;width:112px;height:95px;background:#222;display:flex;align-items:center;justify-content:center;gap:10px;color:#ccc;font-size:11px}
.lang .flag{width:24px;height:16px;background:linear-gradient(135deg,#203a7a,#b8223a)}

/* hero */
.hero{left:0;top:138px;width:1200px;height:470px;background:linear-gradient(110deg,#8b7660 0%,#c9c2b8 40%,#e9e6e1 70%,#d7d2cb 100%)}
.hero-caption{left:0;top:340px;width:532px;height:121px;background:rgba(20,20,20,.72);padding:14px 0 0 99px;color:var(--white)}
.hero-caption h1{font-family:"Philosopher",sans-serif;font-weight:400;font-size:38px;line-height:44px}
.hero-caption p{font-size:13px;line-height:22px;color:#ddd;width:420px}

/* estimate */
.estimate{left:0;top:608px;width:1200px;height:87px;background:var(--black)}
.estimate p{left:101px;top:30px;font-size:19px;color:var(--white)}
.estimate .btn{left:959px;top:27px;width:124px;height:34px;line-height:34px;font-size:13px}

/* section titles */
.section-title{font-family:"Philosopher",sans-serif;font-size:35px;color:var(--ink);display:flex;align-items:center;gap:12px;font-weight:400}
.section-title .mark{width:26px;height:26px;background:var(--orange)}
.section-title em{font-style:normal;color:var(--orange)}
.services-title{left:0;top:760px;width:1200px;justify-content:center}
.title-rule{height:3px;background:#999}
.services-rule{left:556px;top:824px;width:88px}

/* service rows */
.photo{background:linear-gradient(135deg,#6d6a66,#b8aea2)}
.service h2{font-family:"Lato",sans-serif;font-weight:400;font-size:23px;color:var(--ink)}
.service .rule{width:58px;height:3px;background:var(--orange);margin:12px 0 18px}
.service p{font-size:13.5px;line-height:24.5px;color:#444}
.service .btn{margin-top:18px;width:94px;height:30px;line-height:30px;font-size:12.5px}
.tags{left:0;width:1200px;display:flex;justify-content:center;gap:20px;font-size:17px;color:#333}
.tags li{list-style:none;display:flex;align-items:center;gap:10px}
.tags li::before{content:"";width:7px;height:7px;border-radius:50%;background:#222}

.stone-bg{left:0;top:1232px;width:1200px;height:376px;background:var(--grey-bg)}

/* about */
.about{left:0;top:1983px;width:1200px;height:374px;background:linear-gradient(90deg,#1f1f1f,#2e2e2e 60%,#242424)}
.about .brand{left:186px;top:210px;font-size:36px}
.about .brand .mark{width:40px;height:40px}
.about .section-title{left:494px;top:70px;width:605px;justify-content:center;color:var(--white)}
.about-rule{left:760px;top:125px;width:88px;background:#bbb}
.about .copy{left:494px;top:158px;width:606px;font-size:13px;line-height:24px;color:#e6e6e6}
.about .sign{left:494px;top:291px;font-size:15px;line-height:23px;color:var(--white)}
.about .sign strong{font-weight:700}

/* footer */
.footer{left:0;top:2357px;width:1200px;height:249px;background:var(--footer)}
.address{left:160px;top:42px;font-size:13px;color:#ddd;line-height:20px}
.address .row{display:flex;gap:14px;margin-bottom:14px}
.address svg{flex:none;margin-top:3px}
.address b{color:var(--white)}
.field{border:1px solid #555;background:var(--field);color:#888;font-size:12px;padding:7px 10px;height:32px;width:209px}
.field.msg{height:60px}
.footer .btn{left:640px;top:147px;width:94px;height:31px;line-height:31px;font-size:13px}
.links{left:950px;top:40px;font-size:13px;color:#ddd;line-height:35px}
.links li{list-style:none;padding-left:22px}
.links li:first-child{padding-left:0;display:flex;gap:8px;align-items:center}

.bottom{left:0;top:2606px;width:1200px;height:53px;background:var(--black)}
.bottom p{left:100px;top:18px;font-size:12px;color:#ccc}
.bottom .socials{right:94px;top:14px}
.bottom .social-dot{width:24px;height:24px}
</style>
</head>
<body>

<header class="abs topbar">
  <div class="abs contact">
    <span><svg width="13" height="13" viewBox="0 0 24 24"><path d="M6.6 10.8a15 15 0 0 0 6.6 6.6l2.2-2.2c.3-.3.7-.4 1-.2 1.1.4 2.3.6 3.6.6.6 0 1 .4 1 1V20c0 .6-.4 1-1 1A17 17 0 0 1 3 4c0-.6.4-1 1-1h3.5c.6 0 1 .4 1 1 0 1.3.2 2.5.6 3.6.1.3 0 .7-.2 1z" fill="#f2652b"/></svg>555-014-2290</span>
    <span><svg width="14" height="12" viewBox="0 0 24 18"><rect x="1" y="1" width="22" height="16" fill="none" stroke="#f2652b" stroke-width="2"/><path d="M1 1l11 9 11-9" fill="none" stroke="#f2652b" stroke-width="2"/></svg>info@praxelun.com</span>
  </div>
  <div class="abs socials" aria-label="Social links">
    <span class="social-dot"></span><span class="social-dot"></span><span class="social-dot"></span><span class="social-dot"></span><span class="social-dot"></span>
  </div>
</header>

<nav class="abs nav">
  <div class="abs brand"><span class="mark"></span>Praxelun</div>
  <ul class="abs menu"><li>Home</li><li>About Us</li><li>Services</li><li>Contact Us</li></ul>
  <div class="abs lang"><span class="flag"></span>English ⌄</div>
</nav>

<section class="abs hero" role="img" aria-label="Craftsman kneeling on a tiled floor, placing a yellow spirit level and rubber mallet"></section>
<div class="abs hero-caption">
  <h1>Welcome To Praxelun</h1>
  <p>Lorem ipsum dolor sit amet, consectetuer adipiscing elit, sed diam nonummy nibh euismod tincidunt ut laoreet dolore magna aliquam</p>
</div>

<section class="abs estimate">
  <p class="abs">Are you Interested in an Estimate?</p>
  <span class="abs btn">GET A QUOTE</span>
</section>

<h2 class="abs section-title services-title"><span class="mark"></span>Our <em>Services</em></h2>
<div class="abs title-rule services-rule"></div>

<!-- Wood works -->
<div class="abs photo" style="left:0;top:863px;width:470px;height:294px" role="img" aria-label="Carpenter in safety glasses cutting a board with a circular saw"></div>
<div class="abs photo" style="left:470px;top:863px;width:108px;height:98px;background:linear-gradient(135deg,#c59a6a,#e8d2b8)" role="img" aria-label="Laying wooden floor planks"></div>
<div class="abs photo" style="left:470px;top:961px;width:108px;height:98px;background:linear-gradient(135deg,#d8d2c8,#8a7a68)" role="img" aria-label="Furnished wooden interior"></div>
<div class="abs photo" style="left:470px;top:1059px;width:108px;height:98px;background:linear-gradient(135deg,#5b6d8a,#c9b26a)" role="img" aria-label="Worker measuring with a level"></div>
<article class="abs service" style="left:620px;top:882px;width:480px">
  <h2>Wood Works</h2><div class="rule"></div>
  <p>Timber is, in essence, a natural and warm material. Wood is also relatively durable and easy to work with, which has made it a favourite of builders throughout history. Our goal is to offer suitable products and quality furniture with installation and after- sales service to all of our clients. In order to achieve this, we're ready to help our clients in all stages of construction from design to production and maintenance.</p>
  <span class="btn">Read More</span>
</article>
<ul class="abs tags" style="top:1178px"><li>Furniture</li><li>Windows</li><li>Doors</li><li>Staircases</li><li>Woodcarving</li><li>Graining</li></ul>

<!-- Stone works -->
<div class="abs stone-bg"></div>
<div class="abs photo" style="left:620px;top:1232px;width:108px;height:292px;background:linear-gradient(180deg,#8a7560,#6b7a5a)" role="img" aria-label="Stone wall and garden path"></div>
<div class="abs photo" style="left:728px;top:1232px;width:472px;height:292px;background:linear-gradient(90deg,#e6e2dc,#8a6a50 55%,#2e2e2e 75%,#a8703e)" role="img" aria-label="Living room with stone fireplace wall and stacked firewood"></div>
<article class="abs service" style="left:97px;top:1261px;width:483px">
  <h2>Stone Works</h2><div class="rule"></div>
  <p>The natural stone found in the ground has been used in construction for centuries because of its durability. A structure built by a skilled craftsman from natural stone is unique, genuine and durable, and perfect for our bracing climate. Our experienced craftsmen are ready to help you in all stages of construction from planning to completion.</p>
  <span class="btn">Read More</span>
</article>
<ul class="abs tags" style="top:1557px"><li>Walls</li><li>Terraces</li><li>Paths</li><li>Outdoor kitchens</li><li>Fireplaces</li><li>Smokeries</li><li>Fences</li></ul>

<!-- Restoration -->
<div class="abs photo" style="left:0;top:1608px;width:470px;height:294px;background:linear-gradient(180deg,#b9d2ea,#a05a3e 55%,#6f5b4a)" role="img" aria-label="Brick building under construction with scaffolding and a crane"></div>
<div class="abs photo" style="left:470px;top:1608px;width:108px;height:98px;background:linear-gradient(135deg,#a07040,#e2c9a0)" role="img" aria-label="Renovated interior with wooden floor"></div>
<div class="abs photo" style="left:470px;top:1706px;width:108px;height:98px;background:linear-gradient(135deg,#e8e4dc,#b0a89a)" role="img" aria-label="Painter renovating a room"></div>
<div class="abs photo" style="left:470px;top:1804px;width:108px;height:98px;background:linear-gradient(180deg,#c8d8e8,#6a6050)" role="img" aria-label="Restored house exterior"></div>
<article class="abs service" style="left:620px;top:1645px;width:480px">
  <h2>Restoration</h2><div class="rule"></div>
  <p>It's good to see that fixing old things has become popular again in recent years and people are trying to find ways to preserve valuable old windows and pieces of furniture before deciding to replace them. It is possible to give a new life to almost any wooden door, window, piece of furniture or staircase. The extensive experience of our craftsmen will help you achieve the desired result.</p>
  <span class="btn">Read More</span>
</article>
<ul class="abs tags" style="top:1922px"><li>Furniture</li><li>Windows</li><li>Doors</li><li>Staircases</li><li>Staircases</li><li>Floors</li><li>Special Projects</li></ul>

<!-- About -->
<section class="abs about" role="img" aria-label="Dim background of a craftsman at work">
  <div class="abs brand"><span class="mark"></span>Praxelun</div>
  <h2 class="abs section-title"><span class="mark" style="background:#fff"></span>About Us</h2>
  <div class="abs title-rule about-rule"></div>
  <p class="abs copy">Praxelun is a company whose business operations include making wooden products, restoration and building structures from natural stone. All of our products are made by craftsmen and specialists who have extensive experience and knowledge in their fields. The products we offer are always handmade and we take the requests and ideas of the specific client into account. We always strive to achieve the best possible quality.</p>
  <p class="abs sign"><strong>Quality matters,</strong><br>Praxelun</p>
</section>

<!-- Footer -->
<footer class="abs footer">
  <div class="abs address">
    <div class="row"><svg width="12" height="16" viewBox="0 0 12 16"><path d="M6 0a6 6 0 0 0-6 6c0 4.5 6 10 6 10s6-5.5 6-10a6 6 0 0 0-6-6zm0 8.5A2.5 2.5 0 1 1 6 3.5a2.5 2.5 0 0 1 0 5z" fill="#f2652b"/></svg><div><b>Praxelun</b><br>Karu 14 10120 Tallinn<br>ESTONIA</div></div>
    <div class="row"><svg width="14" height="14" viewBox="0 0 24 24"><path d="M6.6 10.8a15 15 0 0 0 6.6 6.6l2.2-2.2c.3-.3.7-.4 1-.2 1.1.4 2.3.6 3.6.6.6 0 1 .4 1 1V20c0 .6-.4 1-1 1A17 17 0 0 1 3 4c0-.6.4-1 1-1h3.5c.6 0 1 .4 1 1 0 1.3.2 2.5.6 3.6.1.3 0 .7-.2 1z" fill="#f2652b"/></svg><div>+372 555 0142</div></div>
    <div class="row"><svg width="14" height="12" viewBox="0 0 24 18"><rect width="24" height="18" fill="#f2652b"/><path d="M1 1l11 9 11-9" fill="none" stroke="#141414" stroke-width="2"/></svg><div>sales@praxelun.com</div></div>
  </div>
  <div class="abs field" style="left:413px;top:45px">Name</div>
  <div class="abs field" style="left:640px;top:45px">Email</div>
  <div class="abs field" style="left:413px;top:96px">Phone</div>
  <div class="abs field" style="left:640px;top:96px">Sublect</div>
  <div class="abs field msg" style="left:413px;top:147px">Message</div>
  <span class="abs btn">Submit</span>
  <ul class="abs links">
    <li><svg width="14" height="14" viewBox="0 0 24 24"><path d="M10 14a5 5 0 0 0 7 0l3-3a5 5 0 0 0-7-7l-1 1M14 10a5 5 0 0 0-7 0l-3 3a5 5 0 0 0 7 7l1-1" fill="none" stroke="#f2652b" stroke-width="2.5"/></svg>Home</li>
    <li>About Us</li><li>Services</li><li>Contact Us</li>
  </ul>
</footer>

<div class="abs bottom">
  <p class="abs">Copyright © 2016 Praxelun. All Rights Reserved.</p>
  <div class="abs socials" aria-label="Social links">
    <span class="social-dot"></span><span class="social-dot"></span><span class="social-dot"></span><span class="social-dot"></span><span class="social-dot"></span>
  </div>
</div>

</body>
</html>
```